Maple Bus Card

i own a building in the bronx ny - its called "Maple 7 on 2 HDFC"i want a classy logo / business card - nothing too religuous but it is like a family there - its a large apartment building - colors i like dark red, black, medium shade of gray also reg business card stuff tel # 914-555-0173 address 4738 Larkwell Ave Bronx NY 10457 Email fijosh@aol.comslogan - " TOGETHER WE ARE HOME "i can send u a picture of the building for the backside

```html
<!DOCTYPE html>
<html lang="en">
<head>
<meta charset="utf-8">
<title>Maple 7 on 2 HDFC – Business Card</title>
<link rel="stylesheet" href="https://fonts.googleapis.com/css2?family=Open+Sans:wght@400;700&display=swap">
<style>
  :root {
    --stage: #3b3b3d;
    --card-dark: #262626;
    --gold: #f2b316;
    --text-light: #f2f2f2;
    --text-gray: #b9b9b9;
    --rule: #8a8a8a;
    --photo-brick: #8a4a3c;
    --photo-leaf: #5f7d4a;
    --photo-street: #6e6f73;
  }
  * { box-sizing: border-box; margin: 0; padding: 0; }
  html, body { width: 1200px; height: 782px; overflow: hidden; }
  body {
    background: var(--stage);
    font-family: "Open Sans", Arial, sans-serif;
    position: relative;
  }
  .card {
    position: absolute;
    top: 236px;
    width: 545px;
    height: 311px;
    overflow: hidden;
    box-shadow: 0 10px 24px rgba(0,0,0,.45);
  }
  .card-front { left: 40px; background: var(--card-dark); }
  .card-back { left: 615px; }

  .accent-bar {
    position: absolute;
    left: 0; right: 0; bottom: 0;
    height: 9px;
    background: var(--gold);
  }

  /* front */
  .brand {
    position: absolute;
    left: 262px;
    top: 118px;
    width: 258px;
    text-align: center;
  }
  .brand-name {
    display: flex;
    align-items: center;
    justify-content: center;
    gap: 10px;
    font-weight: 400;
    font-size: 24px;
    letter-spacing: .5px;
    line-height: 32px;
    color: var(--gold);
    white-space: nowrap;
  }
  .brand-mark {
    width: 12px; height: 12px;
    background: var(--gold);
    flex: none;
  }
  .brand-type {
    display: flex;
    align-items: center;
    gap: 10px;
    margin-top: 4px;
    font-weight: 700;
    font-size: 16px;
    line-height: 22px;
    color: var(--text-light);
    letter-spacing: 1px;
  }
  .brand-type::before,
  .brand-type::after {
    content: "";
    flex: 1;
    height: 1px;
    background: var(--rule);
  }
  .slogan {
    margin-top: 6px;
    font-weight: 700;
    font-size: 14px;
    line-height: 20px;
    letter-spacing: 1.4px;
    color: var(--text-gray);
    white-space: nowrap;
  }

  .contact {
    position: absolute;
    left: 28px;
    top: 170px;
    list-style: none;
    color: var(--text-light);
    font-size: 13px;
    line-height: 22px;
  }
  .contact li { display: flex; align-items: center; gap: 7px; white-space: nowrap; }
  .contact svg { width: 12px; height: 12px; fill: var(--gold); flex: none; }

  .address {
    position: absolute;
    right: 25px;
    top: 226px;
    text-align: right;
    font-style: normal;
    color: var(--text-light);
    font-size: 15px;
    line-height: 21px;
    white-space: nowrap;
  }

  /* back */
  .building-photo {
    position: absolute;
    inset: 0 0 9px 0;
    background:
      linear-gradient(180deg, rgba(95,125,74,.85) 0%, rgba(95,125,74,0) 38%),
      linear-gradient(180deg, var(--photo-brick) 20%, #7a4236 70%, var(--photo-street) 100%);
  }
</style>
</head>
<body>

  <section class="card card-front" aria-label="Business card front">
    <div class="brand">
      <div class="brand-name"><span class="brand-mark"></span>Maple 7 on 2</div>
      <div class="brand-type">HDFC</div>
      <div class="slogan">TOGETHER WE ARE HOME</div>
    </div>

    <ul class="contact">
      <li>
        <svg viewBox="0 0 24 24" aria-hidden="true"><path d="M6.6 10.8a15.1 15.1 0 0 0 6.6 6.6l2.2-2.2a1 1 0 0 1 1-.25 11.4 11.4 0 0 0 3.6.57 1 1 0 0 1 1 1V20a1 1 0 0 1-1 1A17 17 0 0 1 3 4a1 1 0 0 1 1-1h3.5a1 1 0 0 1 1 1c0 1.25.2 2.45.57 3.57a1 1 0 0 1-.25 1z"/></svg>
        914-555-0173
      </li>
      <li>
        <svg viewBox="0 0 24 24" aria-hidden="true"><path d="M2 5h20v14H2z M3.5 6.5v.4L12 13l8.5-6.1v-.4z" fill-rule="evenodd"/></svg>
        mavreld@quintmail.com
      </li>
    </ul>

    <address class="address">4738 Larkwell Ave<br>Bronx NY 10457</address>

    <div class="accent-bar"></div>
  </section>

  <section class="card card-back" aria-label="Business card back">
    <div class="building-photo" role="img" aria-label="Photograph of the red-brick apartment building with trees and parked cars on the street"></div>
    <div class="accent-bar"></div>
  </section>

</body>
</html>
```